Dry Cleaners Pick-up & Delivery Service

We are in the need of a post card design to hand out in public focused in our dry-cleaners pick up and delivery business services. The postcard must include a price list of most common items sent to the dry cleaners on a regular basis along with promotional sign-up deals and specials as advertised on our website. The color palette must match our website's color scheme - www.tovrastik.com - we would like to focus on our free pick-up and free delivery service. The hand out post card should look clean, organized and neat, yet modern in style projecting the cleanliness of the clothing articles that our customer let us take care of saving them time while we take care of this errand for them. All new customers receive a free high quality, heavy duty laundry bag with our business information and are encouraged to request for $10 of free dry cleaning on their first order, no strings attached, just for signing up to our service.We strive to please our customers and invest on them to have more free time on their hands, plain and simple. We also offer law enforcement uniform special, as the area we focus our routes is a high law enforcement residential community. The logo is attached and must be visible in the postcard as well as the website address and phone number 305-471-2093 as these are the main contact forms of clients reaching our business. This is home based business, we have a partnership with a dry cleaners business who does all of our route customers' dry cleaning needs. Our business is all about the marketing, sales and networking with corporate businesses. The postcard handout must have designs of both sides of the post card as well. They will not be used for mailing for the moment being, they will be only used to hand out.

Industry/Entity Type

Dry Cleaning

```html
<!DOCTYPE html>
<html lang="en">
<head>
<meta charset="utf-8">
<title>Tovrastik Postcard – Front and Back</title>
<link href="https://fonts.googleapis.com/css2?family=Mulish:wght@400;600;700;800;900&display=swap" rel="stylesheet">
<style>
  :root {
    --bg: #e9e9e7;
    --card: #f7f7f7;
    --ink: #1d1d1b;
    --muted: #555555;
    --green: #6ab547;
    --green-dark: #4f9a34;
    --band: #d9d9d9;
    --line: #9a9a9a;
    --shirt-light: #c9d8ea;
    --shirt-dark: #3e5778;
    --basket: #6e4a34;
    --towel: #c9c3b4;
  }
  * { box-sizing: border-box; margin: 0; padding: 0; }
  html, body { width: 1200px; height: 903px; overflow: hidden; }
  body {
    background: var(--bg);
    font-family: "Mulish", Arial, sans-serif;
    color: var(--ink);
    position: relative;
  }
  .card {
    position: absolute;
    background: var(--card);
    overflow: hidden;
  }
  .card--front { left: 280px; top: 17px; width: 443px; height: 569px; }
  .card--back { left: 734px; top: 68px; width: 449px; height: 568px; }

  /* Front */
  .shirts-photo {
    position: absolute; left: 0; top: 0; width: 100%; height: 171px;
    background: linear-gradient(90deg, var(--shirt-light) 0%, #e6edf5 18%, var(--shirt-dark) 38%, #7f9cc4 55%, #f1f3f6 72%, var(--shirt-light) 88%, #a9c0dd 100%);
  }
  .service-band {
    position: absolute; left: 0; top: 171px; width: 100%; height: 38px;
    background: var(--band);
    display: flex; align-items: center; justify-content: center;
    font-weight: 800; font-size: 17px;
  }
  .brand-name {
    position: absolute;
    font-weight: 800; color: var(--ink);
    letter-spacing: 0.5px;
    display: flex; align-items: center; gap: 10px;
  }
  .brand-name__dot { width: 14px; height: 14px; border-radius: 50%; background: var(--green); }
  .card--front .brand-name { left: 28px; top: 230px; font-size: 40px; }
  .signup {
    position: absolute; text-align: left; color: var(--green);
  }
  .signup__title { font-weight: 800; font-size: 13px; letter-spacing: 0.6px; }
  .signup__call { font-weight: 800; font-size: 11px; letter-spacing: 0.3px; }
  .card--front .signup { left: 300px; top: 248px; }

  .perk-list { position: absolute; left: 32px; top: 310px; list-style: none; }
  .perk-list li {
    display: flex; align-items: center; gap: 6px;
    font-weight: 900; font-size: 16px; height: 34px; text-transform: uppercase;
  }
  .perk-list svg { width: 18px; height: 18px; }

  .basket-photo {
    position: absolute; left: 0; bottom: 0; width: 172px; height: 126px;
    background: linear-gradient(180deg, var(--towel) 0%, #9aa79e 35%, var(--basket) 55%, #4a2f20 100%);
    border-top-right-radius: 30px;
  }
  .offer {
    position: absolute; left: 216px; top: 437px; width: 212px; height: 115px;
    background: var(--green); border-radius: 6px; color: #fff;
    padding: 8px;
  }
  .offer__tail {
    position: absolute; left: 30px; top: -16px; width: 30px; height: 18px;
  }
  .offer__inner {
    border: 1px dashed rgba(255,255,255,0.9); border-radius: 4px;
    height: 100%; padding: 22px 10px 6px;
  }
  .offer__text { font-size: 9.5px; font-weight: 700; line-height: 1.25; color: var(--ink); }
  .offer__amount { font-size: 15px; font-weight: 900; }
  .offer__url { margin-top: 7px; text-align: center; font-weight: 900; font-size: 13px; color: #fff; }

  /* Back */
  .card--back .brand-name { left: 26px; top: 24px; font-size: 38px; }
  .card--back .signup { left: 262px; top: 32px; color: var(--ink); }
  .card--back .signup__title { font-size: 15px; }
  .card--back .signup__call { font-size: 13px; }
  .pricing-heading {
    position: absolute; left: 32px; top: 114px;
    font-size: 8.5px; font-weight: 600; color: var(--muted); text-transform: uppercase;
  }
  .price-col { position: absolute; top: 131px; }
  .price-col--women { left: 32px; width: 176px; }
  .price-col--men { left: 240px; width: 170px; }
  .price-col__title { font-size: 9px; font-weight: 800; text-transform: uppercase; margin-bottom: 8px; }
  .price-divider { position: absolute; left: 224px; top: 131px; width: 1px; height: 300px; background: var(--line); }
  .price-item { display: flex; justify-content: space-between; padding-left: 8px; height: 20.3px; }
  .price-item__name { font-size: 9.5px; font-weight: 600; line-height: 1.05; }
  .price-item__note { display: block; font-size: 6px; font-weight: 400; color: var(--muted); }
  .price-item__size { font-size: 6px; font-weight: 400; }
  .price-item__price { font-size: 9.5px; font-weight: 600; }
  .price-item--special .price-item__name { text-transform: uppercase; }
  .fine-print { padding-left: 8px; margin: 16px 0 22px; font-size: 5.5px; line-height: 1.3; color: var(--muted); }
  .price-gap { height: 14px; }
  .card--back .basket-photo { width: 150px; height: 112px; }
  .back-url {
    position: absolute; right: 26px; bottom: 18px;
    color: var(--green); font-weight: 800; font-size: 21px;
  }
</style>
</head>
<body>

<section class="card card--front" aria-label="Postcard front">
  <div class="shirts-photo" role="img" aria-label="Row of pressed dress shirts in white and blue tones on hangers"></div>
  <div class="service-band">Dry Cleaners Pick up &amp; Delivery Services</div>
  <div class="brand-name">Tovrastik<span class="brand-name__dot"></span></div>
  <div class="signup">
    <div class="signup__title">SIGN-UP FREE!</div>
    <div class="signup__call">CALL 305-471-2093</div>
  </div>
  <ul class="perk-list">
    <li><svg viewBox="0 0 18 18"><path d="M2 10 L7 15 L16 2" fill="none" stroke="#1d1d1b" stroke-width="2.4" stroke-linecap="round"/></svg>Free pick-up!</li>
    <li><svg viewBox="0 0 18 18"><path d="M2 10 L7 15 L16 2" fill="none" stroke="#1d1d1b" stroke-width="2.4" stroke-linecap="round"/></svg>Free delivery!</li>
    <li><svg viewBox="0 0 18 18"><path d="M2 10 L7 15 L16 2" fill="none" stroke="#1d1d1b" stroke-width="2.4" stroke-linecap="round"/></svg>Next-day service available!</li>
  </ul>
  <div class="basket-photo" role="img" aria-label="Wicker laundry basket with folded towels"></div>
  <div class="offer">
    <svg class="offer__tail" viewBox="0 0 30 18"><path d="M0 0 L30 18 L8 18 Z" fill="#6ab547"/></svg>
    <div class="offer__inner">
      <p class="offer__text"><span class="offer__amount">$10</span> of free dry cleaning<br>on your first order, no strings attached,<br>just for signing up to our service.</p>
      <p class="offer__url">www.tovrastik.com</p>
    </div>
  </div>
</section>

<section class="card card--back" aria-label="Postcard back">
  <div class="brand-name">Tovrastik<span class="brand-name__dot"></span></div>
  <div class="signup">
    <div class="signup__title">SIGN-UP FREE!</div>
    <div class="signup__call">CALL 305-471-2093</div>
  </div>
  <p class="pricing-heading">Dry cleaning pricing:</p>

  <div class="price-col price-col--women">
    <p class="price-col__title">Women</p>
    <div class="price-item"><span class="price-item__name">Dress<span class="price-item__note">Dry-Cleaned and Pressed</span></span><span class="price-item__price">$10.95</span></div>
    <div class="price-item"><span class="price-item__name">Women Blouse<span class="price-item__note">Dry-Cleaned &amp; Pressed</span></span><span class="price-item__price">$4.95</span></div>
    <div class="price-item"><span class="price-item__name">Women Casual Pants/Jeans<span class="price-item__note">Dry-Cleaned &amp; Pressed</span></span><span class="price-item__price">$4.95</span></div>
    <div class="price-item"><span class="price-item__name">Skirt - Long<span class="price-item__note">Dry-Cleaned &amp; Pressed</span></span><span class="price-item__price">$6.49</span></div>
    <div class="price-item"><span class="price-item__name">Skirt - Short<span class="price-item__note">Dry-Cleaned &amp; Pressed</span></span><span class="price-item__price">$4.95</span></div>
    <div class="price-item"><span class="price-item__name">Women Suit<span class="price-item__note">2 piece - Dry-Cleaned &amp; Pressed</span></span><span class="price-item__price">$10.95</span></div>
    <div class="price-item"><span class="price-item__name">Women Evening/Formal Dress<span class="price-item__note">Subject to surcharge (beads, etc)</span></span><span class="price-item__price">$28.99</span></div>
    <p class="fine-print">Silk, linen and fur items may carry a surcharge of up to $5.00 each.<br>Items with beads or attached accessories may cost up to $4.50 more per garment.<br>Please note any stains when placing your order.</p>
    <div class="price-item"><span class="price-item__name">Pillow Covers<span class="price-item__note">Any size</span></span><span class="price-item__price">$2.99</span></div>
    <div class="price-item"><span class="price-item__name">Table Cloths &amp; Runners <span class="price-item__size">(Large)</span></span><span class="price-item__price">$11.95</span></div>
    <div class="price-item"><span class="price-item__name">Table Cloth &amp; Runners <span class="price-item__size">(Small)</span></span><span class="price-item__price">$9.99</span></div>
  </div>

  <div class="price-divider"></div>

  <div class="price-col price-col--men">
    <p class="price-col__title">Men</p>
    <div class="price-item"><span class="price-item__name">Men's Shirt (100% cotton)<span class="price-item__note">Laundered &amp; Pressed</span></span><span class="price-item__price">$2.99</span></div>
    <div class="price-item"><span class="price-item__name">Men Business Shirt<span class="price-item__note">Dry-Cleaned &amp; Pressed</span></span><span class="price-item__price">$4.50</span></div>
    <div class="price-item"><span class="price-item__name">Men Business Pants<span class="price-item__note">Dry-Cleaned &amp; Pressed</span></span><span class="price-item__price">$4.95</span></div>
    <div class="price-item"><span class="price-item__name">Men Business Vest<span class="price-item__note">Dry-Cleaned &amp; Pressed</span></span><span class="price-item__price">$4.95</span></div>
    <div class="price-item"><span class="price-item__name">Men Pants/Jeans<span class="price-item__note">Dry-Cleaned &amp; Pressed</span></span><span class="price-item__price">$4.95</span></div>
    <div class="price-item"><span class="price-item__name">Men Suit<span class="price-item__note">2-Piece - Dry-Cleaned &amp; Pressed</span></span><span class="price-item__price">$10.95</span></div>
    <div class="price-item"><span class="price-item__name">3 piece suit<span class="price-item__note">Dry-Cleaned &amp; Pressed</span></span><span class="price-item__price">$15.95</span></div>
    <div class="price-item"><span class="price-item__name">Tie<span class="price-item__note">Dry-Cleaned &amp; Pressed</span></span><span class="price-item__price">$3.95</span></div>
    <div class="price-item"><span class="price-item__name">Sports Coat/Jacket<span class="price-item__note">Dry-Cleaned &amp; Pressed</span></span><span class="price-item__price">$6.95</span></div>
    <div class="price-item"><span class="price-item__name">Men Guayabera<span class="price-item__note">Laundered and Pressed</span></span><span class="price-item__price">$6.99</span></div>
    <div class="price-gap"></div>
    <div class="price-item price-item--special" style="height:36px"><span class="price-item__name">Law Enforcement Special<span class="price-item__note">1 LEO shirt with 1 LEO pair of pants<br>Dry-Cleaned and Pressed</span></span><span class="price-item__price">$7.99</span></div>
    <div class="price-item price-item--special" style="height:44px"><span class="price-item__name">Wash &amp; Fold Pricing<br><span style="text-transform:none">Regular Clothing Articles</span><span class="price-item__note">1 LEO shirt with 1 LEO pair of pants<br>Dry-Cleaned and Pressed</span></span><span class="price-item__price">$1.99</span></div>
  </div>

  <div class="basket-photo" role="img" aria-label="Wicker laundry basket with folded towels"></div>
  <p class="back-url">www.tovrastik.com</p>
</section>

</body>
</html>
```